LM-Steuerberatung WordPress Site fully implemented (tax advisor)

Hello!
I need a little Wordpress Site for my newly founded Tax-Advisor Company.
I am a one-man Office advising in the area of Crypto-Currency.
PLEASE only provide a Design, if you can also Implement a WP-Site afterwards on an existing Webspace.

Please find the Content and Website-Description in the attached Document

Language for the Website is German (for now)

Target Market(s)

Tax-Advisory (specialized in Crypto Currency)

Coding

Coded - Design and coding required

Number of Pages Required

5+ page

Font styles to use
Sans Serif

Requirements
Must have
• Wordpress Implementation afterwards - Details according to attached Project Information Document

```html
<!DOCTYPE html>
<html lang="de">
<head>
<meta charset="utf-8">
<title>LM-Steuerberatung</title>
<link rel="stylesheet" href="https://fonts.googleapis.com/css2?family=Montserrat:wght@600;800&family=Roboto:wght@400;500&family=Roboto+Condensed:wght@500;700&display=swap">
<style>
:root{
  --navy:#1c2a40;
  --ink:#1d2635;
  --gray:#a7a7a7;
  --band:#12103a;
  --footer:#0e0b2a;
  --white:#ffffff;
}
*{margin:0;padding:0;box-sizing:border-box}
html,body{width:1200px;height:878px;overflow:hidden;background:var(--white)}
body{position:relative;font-family:'Roboto',sans-serif}
.top-rule{position:absolute;left:0;top:0;width:1200px;height:4px;background:var(--gray)}
.site-header{position:absolute;left:0;top:4px;width:1200px;height:94px;background:var(--white)}
.brand{position:absolute;left:144px;top:28px;display:flex;align-items:center;gap:12px}
.brand-mark{width:30px;height:30px;background:var(--navy)}
.brand-name{font-family:'Montserrat',sans-serif;font-weight:600;font-size:21px;letter-spacing:1px;color:var(--ink);white-space:nowrap}
.lang{position:absolute;left:1013px;top:18px;display:flex;align-items:center;gap:8px}
.flag{width:22px;height:13px;background:linear-gradient(#000 0 33%,#d00 33% 66%,#fc0 66%)}
.caret{width:0;height:0;border-left:5px solid transparent;border-right:5px solid transparent;border-top:6px solid var(--ink)}
.main-nav{position:absolute;top:46px;left:574px;display:flex;font-size:14.5px;font-weight:500;color:var(--ink)}
.main-nav span{position:absolute;white-space:nowrap;display:flex;align-items:center;gap:7px}
.hero{position:absolute;left:0;top:98px;width:1200px;height:540px;background:radial-gradient(ellipse at 78% 45%,#3d4fc8 0%,#3a2f92 35%,#2a1f62 70%,#241a52 100%)}
.hero-shape{position:absolute;left:0;top:0}
.hero-copy{position:absolute;left:145px;top:140px;width:490px;color:var(--white)}
.hero-title{font-family:'Montserrat',sans-serif;font-weight:800;font-size:38px;line-height:50px;letter-spacing:0;white-space:nowrap}
.hero-lead{margin-top:32px;font-size:21px;line-height:27px;text-align:justify}
.hero-button{position:absolute;left:145px;top:351px;width:309px;height:46px;background:var(--gray);color:var(--white);font-family:'Roboto Condensed',sans-serif;font-weight:700;font-size:15px;display:flex;align-items:center;justify-content:center}
.ticker{position:absolute;left:0;top:638px;width:1200px;height:50px;background:var(--band);color:var(--white);font-family:'Roboto Condensed',sans-serif;font-weight:700;font-size:19.5px;display:flex;align-items:center;justify-content:center}
.ticker svg{position:absolute;top:11px}
.site-footer{position:absolute;left:0;top:688px;width:1200px;height:184px;background:var(--footer);color:var(--white);text-align:center}
.footer-nav{margin-top:42px;font-family:'Roboto Condensed',sans-serif;font-weight:700;font-size:20px;word-spacing:2px}
.footer-nav i{font-style:normal;margin:0 22px}
.copyright{margin-top:18px;font-size:13.6px}
.social{margin-top:20px;display:flex;justify-content:center;gap:13px}
.social span{width:30px;height:30px;border-radius:50%;background:#cfcfcf}
.bottom-rule{position:absolute;left:0;top:872px;width:1200px;height:6px;background:var(--gray)}
</style>
</head>
<body>
<div class="top-rule"></div>
<header class="site-header">
  <div class="brand"><span class="brand-mark"></span><span class="brand-name">LM STEUERBERATUNG</span></div>
  <div class="lang"><span class="flag"></span><span class="caret"></span></div>
  <nav class="main-nav">
    <span style="left:0">HOME</span>
    <span style="left:73px">LEISTUNGEN <i class="caret"></i></span>
    <span style="left:192px">ÜBER MICH</span>
    <span style="left:300px">KONTAKT</span>
    <span style="left:397px">IMPRESSUM</span>
  </nav>
</header>
<section class="hero" role="img" aria-label="Illustration eines Laptops mit Finanzdiagrammen und Datenanalyse">
  <svg class="hero-shape" width="1200" height="540" viewBox="0 0 1200 540">
    <polygon fill="var(--gray)" points="48,102 176,34 244,72 660,72 756,186 620,474 244,474 184,510 48,438"/>
    <polygon fill="var(--navy)" points="64,116 184,50 244,72 660,72 732,186 620,474 244,474 184,498 64,430"/>
  </svg>
  <div class="hero-copy">
    <h1 class="hero-title">WILLKOMMEN BEI<br>LM-STEUERBERATUNG!</h1>
    <p class="hero-lead">Ihrem Spezialisten bei allen steuerlichen Themen rund um Einkünfte &amp; Vermögen aus Krypto-Assets.</p>
  </div>
  <div class="hero-button">WEITER ZU UNSEREN LEISTUNGEN</div>
</section>
<div class="ticker">
  <svg style="left:158px" width="16" height="30" viewBox="0 0 16 30"><polyline points="14,2 2,15 14,28" fill="none" stroke="#fff" stroke-width="2"/></svg>
  Dann mach ich eine Schweizer Holding-Gesellschaft– dort zahlt man fast keine Steuern
  <svg style="left:1025px" width="16" height="30" viewBox="0 0 16 30"><polyline points="2,2 14,15 2,28" fill="none" stroke="#fff" stroke-width="2"/></svg>
</div>
<footer class="site-footer">
  <nav class="footer-nav">HOME<i>/</i>LEISTUNGEN<i>/</i>ÜBER MICH<i>/</i>KONTAKT<i>/</i>IMPRESSUM</nav>
  <p class="copyright">© 2022 LM-Steuerberatung. All rights reserved.Privacy &nbsp;|&nbsp; Terms of Use</p>
  <div class="social"><span></span><span></span><span></span></div>
</footer>
<div class="bottom-rule"></div>
</body>
</html>
```